BUSINESS CARD DESIGN

NAME- DALE VORSKIN
PHONE NUMER - 555- 714-9082
EMAIL- OFFICE@TRV-GROUNDMAKRZ.COM
BACK OF CARD- SPEACIALIZES IN LAND CLEARING, FORESTRY MUCLHING AND EXCAVATION

Contact Information for Business Card

NAME- DALE VORSKIN PHONE NUMER - 555- 714-9082 EMAIL- OFFICE@TRV-GROUNDMAKRZ.COM BACK OF CARD- SPEACIALIZES IN LAND CLEARING , MUCLHING AND EXCAVATION

```html
<!DOCTYPE html>
<html lang="en">
<head>
<meta charset="utf-8">
<title>Terravale Groundmakrz – Business Card</title>
<link rel="stylesheet" href="https://fonts.googleapis.com/css2?family=Montserrat:wght@400;500;700&display=swap">
<style>
  :root {
    --backdrop: #5b4532;
    --card-white: #ffffff;
    --card-black: #070707;
    --ink: #111111;
    --accent: #f7b218;
    --faint-grey: #dcdcdc;
    --emboss: #1c1c1c;
  }
  html, body {
    margin: 0;
    padding: 0;
    width: 900px;
    height: 1200px;
    overflow: hidden;
    background: var(--backdrop);
    font-family: "Montserrat", sans-serif;
  }
  .canvas {
    position: relative;
    width: 900px;
    height: 1200px;
  }
  .card {
    position: absolute;
    border-radius: 22px;
    overflow: hidden;
    box-shadow: 0 8px 18px rgba(0,0,0,0.45);
  }
  .card--front {
    left: 80px; top: 131px;
    width: 742px; height: 440px;
    background: var(--card-white);
  }
  .card--back {
    left: 78px; top: 638px;
    width: 744px; height: 442px;
    background: var(--card-black);
  }
  .brand {
    position: absolute;
    display: flex;
    flex-direction: column;
    align-items: center;
    text-align: center;
    font-weight: 700;
  }
  .brand__circle {
    border-radius: 50%;
  }
  .brand--front {
    left: 52px; top: 22px; width: 236px;
    color: var(--ink);
  }
  .brand--front .brand__circle {
    width: 108px; height: 108px;
    border: 6px solid var(--ink);
    box-sizing: border-box;
    margin-bottom: 14px;
  }
  .brand--front .brand__name {
    font-size: 21px; line-height: 1.15; letter-spacing: 0.5px;
  }
  .brand--front .brand__phone {
    font-size: 12px; letter-spacing: 5px; margin-top: 6px;
  }
  .watermark {
    position: absolute;
    left: 410px; top: 150px;
    width: 310px; height: 310px;
    border-radius: 50%;
    border: 16px solid var(--faint-grey);
    box-sizing: border-box;
  }
  .holder {
    position: absolute;
    left: 43px; top: 262px;
  }
  .holder__name {
    margin: 0;
    font-size: 26px; font-weight: 700;
    color: var(--accent);
    letter-spacing: 0.3px;
  }
  .holder__title {
    margin: 4px 0 14px;
    font-size: 16.5px; font-weight: 400;
    color: var(--ink);
  }
  .contact {
    list-style: none; margin: 0; padding: 0;
  }
  .contact__item {
    display: flex; align-items: center;
    font-size: 16px; color: var(--ink);
    height: 28px;
  }
  .contact__icon {
    width: 15px; height: 15px;
    margin-right: 9px;
    fill: var(--accent);
  }
  .brand--back {
    left: 172px; top: 82px; width: 400px;
    color: var(--emboss);
  }
  .brand--back .brand__circle {
    width: 190px; height: 190px;
    border: 10px solid var(--emboss);
    box-sizing: border-box;
    margin-bottom: 18px;
  }
  .brand--back .brand__name {
    font-size: 30px; line-height: 1.15; letter-spacing: 1px;
  }
  .brand--back .brand__phone {
    font-size: 15px; letter-spacing: 8px; margin-top: 8px;
  }
</style>
</head>
<body>
<main class="canvas">

  <section class="card card--front" aria-label="Card front">
    <div class="brand brand--front">
      <div class="brand__circle"></div>
      <div class="brand__name">TERRAVALE<br>GROUNDMAKRZ LLC</div>
      <div class="brand__phone">555-714-9082</div>
    </div>

    <div class="watermark" aria-hidden="true"></div>

    <div class="holder">
      <h1 class="holder__name">DALE VORSKIN</h1>
      <p class="holder__title">Managing Director</p>
      <ul class="contact">
        <li class="contact__item">
          <svg class="contact__icon" viewBox="0 0 24 24" aria-hidden="true"><path d="M6.6 10.8a15.1 15.1 0 0 0 6.6 6.6l2.2-2.2a1 1 0 0 1 1-.25 11.4 11.4 0 0 0 3.6.57 1 1 0 0 1 1 1V20a1 1 0 0 1-1 1A17 17 0 0 1 3 4a1 1 0 0 1 1-1h3.5a1 1 0 0 1 1 1c0 1.25.2 2.45.57 3.57a1 1 0 0 1-.25 1z"/></svg>
          555- 714-9082
        </li>
        <li class="contact__item">
          <svg class="contact__icon" viewBox="0 0 24 24" aria-hidden="true"><path d="M2 6h20v12H2z" opacity="1"/><path d="M2 6l10 7 10-7" fill="none" stroke="#fff" stroke-width="1.6"/></svg>
          OFFICE@TRV-GROUNDMAKRZ.COM
        </li>
        <li class="contact__item">
          <svg class="contact__icon" viewBox="0 0 24 24" aria-hidden="true"><circle cx="12" cy="12" r="10"/><path d="M2 12h20M12 2c3 3 3 17 0 20M12 2c-3 3-3 17 0 20" fill="none" stroke="#fff" stroke-width="1.4"/></svg>
          WWW.TRV-GROUNDMAKRZ.COM
        </li>
      </ul>
    </div>
  </section>

  <section class="card card--back" aria-label="Card back">
    <div class="brand brand--back">
      <div class="brand__circle"></div>
      <div class="brand__name">TERRAVALE<br>GROUNDMAKRZ LLC</div>
      <div class="brand__phone">555-714-9082</div>
    </div>
  </section>

</main>
</body>
</html>
```